Motor Oil Lubricant Package Labels

We are looking for a logo and label that we can put on our motor oil bottle 1 liter and 5 liter. The name of our motor oil is Corvana. We want to design our flagship logo for CORVANA MOTOR OILS and as well as the label that will go on the bottle. We have some drafts that we have come up with attached and would like to see more options. The concept of a timeless motor oil and the endless loop of lubricating oils incorporated in the design. We will have full synthetic motor oil, a synthetic blend motor, ATF III transmission fluid, KRL-VI transmission fluid. hydraulic oils etc. Examples will be attached
Target Market(s)
Automotive Lubricants and Chemicals
Industry/Entity Type
Automotive
Logo Text
Corvana Lubricants
Font styles to use
Other font styles liked:
- Let designer choose
Requirements
Must have
- The Corvana sign incorporated in a very cool way to our name. Our brand needs to stick out
Nice to have
- Automotive lubricant related and colors red, white, and blue incorporated in the design
Should not have
- Images of individuals and or topics not related to automotive lubricants.

```html
<!DOCTYPE html>
<html lang="en">
<head>
<meta charset="utf-8">
<title>Corvana Motor Oil Labels</title>
<link rel="stylesheet" href="https://fonts.googleapis.com/css2?family=Oswald:wght@500;700&family=Roboto:wght@500&display=swap">
<style>
  :root {
    --page: #e8e9ea;
    --page-light: #f7f7f7;
    --gold-dark: #b38a1e;
    --gold: #d9b345;
    --gold-light: #f4e29a;
    --red: #ec1c24;
    --blue: #2b4fa3;
    --ink: #111111;
    --white: #ffffff;
    --edge: #cfd6de;
  }
  * { margin: 0; padding: 0; box-sizing: border-box; }
  html, body { width: 1200px; height: 935px; overflow: hidden; }
  body {
    background: radial-gradient(ellipse at center, var(--page-light) 0%, var(--page) 75%);
    position: relative;
  }
  .label { position: absolute; top: 116px; width: 432px; height: 702px; }
  .label--front { left: 140px; }
  .label--back { left: 624px; }
  .label svg { display: block; width: 432px; height: 702px; overflow: visible; }
  .brand-name { font-family: "Oswald", sans-serif; font-weight: 700; fill: var(--ink); }
  .spec-small { font-family: "Oswald", sans-serif; font-weight: 700; fill: var(--white); letter-spacing: 1px; }
  .spec-grade { font-family: "Oswald", sans-serif; font-weight: 700; fill: var(--white); }
  .seal-text { font-family: "Oswald", sans-serif; font-weight: 700; fill: var(--ink); }
  .volume { font-family: "Oswald", sans-serif; font-weight: 700; fill: var(--ink); }
  .origin { font-family: "Oswald", sans-serif; font-weight: 700; fill: #fff4d6; }
  .flag-caption { font-family: "Roboto", sans-serif; font-weight: 500; fill: var(--ink); }
</style>
</head>
<body>

<svg width="0" height="0" style="position:absolute">
  <defs>
    <linearGradient id="gold-metal" x1="0" y1="0" x2="1" y2="0">
      <stop offset="0" stop-color="#c9a23a"/>
      <stop offset="0.3" stop-color="#f2dc8c"/>
      <stop offset="0.55" stop-color="#d8b247"/>
      <stop offset="0.8" stop-color="#c19628"/>
      <stop offset="1" stop-color="#e6c86a"/>
    </linearGradient>
    <radialGradient id="seal-ring" cx="0.5" cy="0.5" r="0.5">
      <stop offset="0.7" stop-color="#f3d98a"/>
      <stop offset="0.9" stop-color="#b07d1c"/>
      <stop offset="1" stop-color="#e9c56a"/>
    </radialGradient>
    <clipPath id="label-shape">
      <rect x="0" y="0" width="432" height="702" rx="34" ry="34"/>
    </clipPath>
  </defs>
</svg>

<div class="label label--front">
  <svg viewBox="0 0 432 702">
    <g clip-path="url(#label-shape)">
      <rect class="label-base" width="432" height="702" fill="url(#gold-metal)"/>
      <path class="band-top-red" d="M92,0 L432,0 L432,102 C330,112 200,70 92,0 Z" fill="var(--red)"/>
      <path class="band-top-blue" d="M235,0 L432,0 L432,72 C380,62 300,32 235,0 Z" fill="var(--blue)" stroke="var(--gold-light)" stroke-width="2"/>
      <path class="band-lower-red" d="M432,118 C330,250 255,330 195,420 C135,520 150,640 215,702 L432,702 Z" fill="var(--red)"/>
      <path class="band-gold-trim" d="M432,118 C330,250 255,330 195,420 C135,520 150,640 215,702" fill="none" stroke="var(--gold)" stroke-width="3"/>
      <path class="band-main-blue" d="M432,92 C360,230 300,320 250,400 C190,480 192,565 250,620 C300,662 380,668 432,662 Z" fill="var(--blue)" stroke="var(--gold-light)" stroke-width="3"/>
      <path class="band-gold-strip" d="M240,640 C310,688 380,690 432,680 L432,690 C380,702 300,700 230,652 Z" fill="var(--gold)"/>
    </g>
    <rect width="432" height="702" rx="34" ry="34" fill="none" stroke="var(--edge)" stroke-width="2"/>

    <text class="brand-name" x="180" y="240" font-size="64" text-anchor="middle">Corvana</text>

    <g class="seal">
      <circle cx="96" cy="394" r="56" fill="url(#seal-ring)"/>
      <circle cx="96" cy="394" r="42" fill="var(--white)" stroke="#d9a521" stroke-width="3"/>
      <text class="seal-text" x="96" y="380" font-size="12" text-anchor="middle">FOR</text>
      <text class="seal-text" x="96" y="396" font-size="12" text-anchor="middle">GASOLINE</text>
      <text class="seal-text" x="96" y="412" font-size="12" text-anchor="middle">ENGIENS</text>
    </g>

    <g class="product-spec">
      <text class="spec-small" transform="translate(318,548) rotate(-90)" font-size="18" textLength="204" lengthAdjust="spacingAndGlyphs">SYNTHETIC BLEND</text>
      <text class="spec-small" transform="translate(390,594) rotate(-90)" font-size="28" textLength="40" lengthAdjust="spacingAndGlyphs">SAE</text>
      <text class="spec-grade" transform="translate(394,548) rotate(-90)" font-size="84" textLength="200" lengthAdjust="spacingAndGlyphs">5W-30</text>
      <text class="spec-small" transform="translate(390,340) rotate(-90)" font-size="28" textLength="62" lengthAdjust="spacingAndGlyphs">APISN</text>
    </g>

    <text class="volume" x="42" y="672" font-size="20">32oz 1946 mU</text>
    <text class="origin" x="204" y="672" font-size="16">Made In USA</text>
  </svg>
</div>

<div class="label label--back">
  <svg viewBox="0 0 432 702">
    <g clip-path="url(#label-shape)">
      <rect class="label-base" width="432" height="702" fill="url(#gold-metal)"/>
      <path class="band-top-red" d="M92,0 L432,0 L432,102 C330,112 200,70 92,0 Z" fill="var(--red)"/>
      <path class="band-top-blue" d="M235,0 L432,0 L432,72 C380,62 300,32 235,0 Z" fill="var(--blue)" stroke="var(--gold-light)" stroke-width="2"/>
      <path class="band-lower-red" d="M432,150 C330,270 250,340 190,440 C130,540 150,645 220,702 L432,702 Z" fill="var(--red)"/>
      <path class="band-gold-trim" d="M432,150 C330,270 250,340 190,440 C130,540 150,645 220,702" fill="none" stroke="var(--gold)" stroke-width="3"/>
      <path class="band-main-blue" d="M432,95 C360,240 300,330 250,410 C190,490 192,570 250,625 C300,665 380,670 432,664 Z" fill="var(--blue)" stroke="var(--gold-light)" stroke-width="3"/>
      <path class="band-gold-strip" d="M240,645 C310,690 380,692 432,682 L432,692 C380,702 300,702 230,656 Z" fill="var(--gold)"/>
    </g>
    <rect width="432" height="702" rx="34" ry="34" fill="none" stroke="var(--edge)" stroke-width="2"/>

    <text class="brand-name" x="146" y="200" font-size="56" text-anchor="middle">Corvana</text>

    <g class="product-spec">
      <text class="spec-small" transform="translate(330,552) rotate(-90)" font-size="18" textLength="190" lengthAdjust="spacingAndGlyphs">SYNTHETIC BLEND</text>
      <text class="spec-small" transform="translate(400,594) rotate(-90)" font-size="28" textLength="40" lengthAdjust="spacingAndGlyphs">SAE</text>
      <text class="spec-grade" transform="translate(404,548) rotate(-90)" font-size="82" textLength="190" lengthAdjust="spacingAndGlyphs">5W-30</text>
      <text class="spec-small" transform="translate(400,350) rotate(-90)" font-size="28" textLength="60" lengthAdjust="spacingAndGlyphs">APISN</text>
    </g>

    <g class="origin-flag" role="img" aria-label="United States flag">
      <rect x="42" y="588" width="84" height="48" fill="var(--white)"/>
      <g fill="#c8102e">
        <rect x="42" y="588" width="84" height="3.7"/>
        <rect x="42" y="595.4" width="84" height="3.7"/>
        <rect x="42" y="602.8" width="84" height="3.7"/>
        <rect x="42" y="610.2" width="84" height="3.7"/>
        <rect x="42" y="617.6" width="84" height="3.7"/>
        <rect x="42" y="625" width="84" height="3.7"/>
        <rect x="42" y="632.3" width="84" height="3.7"/>
      </g>
      <rect x="42" y="588" width="36" height="26" fill="#1f3a7a"/>
      <rect x="42" y="636" width="84" height="14" fill="var(--white)"/>
      <text class="flag-caption" x="84" y="647" font-size="10.5" text-anchor="middle" letter-spacing="0.5">MADE  IN  USA</text>
    </g>
  </svg>
</div>

</body>
</html>
```